Boutique Store Selling Antiques and Unique Finds

I need a Web Page designed for my Store Called "Willow Lane". I would like a very classic, muted design that looks European when pulled up. I will be selling Antiques from all over the world and Unique finds that have reproduced. I will also be selling high-end purses and jewelry with unique, reasonable products for the every-day buyer as well.

Target Market(s)

25-70 year old men and women;)

Coding

Coded - Design and coding required

Number of Pages Required

1 page

Colors

Designer to choose only greyscale colors for use in the design.

Requirements
Must have
• I want it

```html
<!DOCTYPE html>
<html lang="en">
<head>
<meta charset="utf-8">
<title>Willow Lane — Antiques &amp; Unique Finds</title>
<link rel="stylesheet" href="https://fonts.googleapis.com/css2?family=Lato:wght@300;400;700&display=swap">
<style>
:root{
  --cream:#fcf8f1;
  --ink:#2a2a2a;
  --muted:#5a5a5a;
  --soft:#8c8a87;
  --line:#a9a6a2;
  --white:#ffffff;
  --label:#f6efe1;
  --footer:#646261;
  --footer-text:#f2f0ec;
}
*{box-sizing:border-box;margin:0;padding:0}
html,body{width:1200px;height:3431px;overflow:hidden}
body{background:var(--cream);font-family:'Lato',sans-serif;color:var(--ink);position:relative}
a{color:inherit;text-decoration:none}
.abs{position:absolute}

/* header */
.site-header{position:absolute;left:0;top:0;width:1200px;height:128px;background:var(--cream)}
.wordmark{position:absolute;left:0;width:1200px;top:46px;text-align:center;font-size:24px;font-weight:400;letter-spacing:5px;text-transform:uppercase;color:var(--ink)}
.utility{position:absolute;top:6px;right:100px;display:flex;gap:34px;align-items:center;font-size:12px;font-weight:300;color:var(--soft)}
.utility span{display:flex;align-items:center;gap:4px}
.main-nav{position:absolute;top:98px;left:0;width:1200px;display:flex;justify-content:center;gap:34px;font-size:13px;letter-spacing:1px;text-transform:uppercase}
.main-nav a{color:var(--ink)}
.main-nav a.active{color:var(--soft)}

/* hero */
.hero{position:absolute;left:0;top:128px;width:1200px;height:514px;background:linear-gradient(180deg,#3b3c3c 0%,#4d4e4d 60%,#6b6a66 80%,#8a8378 100%)}
.hero-photo{position:absolute;left:540px;top:90px;width:420px;height:424px;background:radial-gradient(ellipse at 50% 45%,#6d6b58 0%,#5a5847 45%,rgba(70,70,62,0) 72%)}
.hero-title{position:absolute;left:117px;top:182px;font-size:37px;font-weight:400;color:var(--white);letter-spacing:1px}
.hero-text{position:absolute;left:120px;top:240px;width:380px;font-size:15px;line-height:24px;color:var(--white)}
.btn{position:absolute;display:flex;align-items:center;justify-content:center;background:var(--white);border-radius:24px;font-size:15px;letter-spacing:1.5px;text-transform:uppercase;color:var(--ink);box-shadow:0 2px 6px rgba(0,0,0,.08)}
.hero .btn{left:120px;top:306px;width:220px;height:48px}
.circle{position:absolute;border-radius:50%;display:flex;align-items:center;justify-content:center}
.hero-arrow{width:62px;height:62px;border:1.5px solid var(--white);top:234px}
.scroll-down{left:568px;top:615px;width:64px;height:64px;background:var(--white);box-shadow:0 2px 6px rgba(0,0,0,.1)}

/* about */
.about-photo{position:absolute;left:112px;top:757px;width:481px;height:427px;background:radial-gradient(ellipse at 40% 50%,#7a6238 0%,#3e2c1a 45%,#1a120c 100%)}
.section-title{position:absolute;font-size:21px;font-weight:400;letter-spacing:1px;text-transform:uppercase;color:var(--ink)}
.about-title{left:638px;top:796px}
.about-text{position:absolute;left:638px;top:845px;width:436px;font-size:13px;font-weight:300;line-height:24px;color:var(--muted)}
.about .btn{left:638px;top:1092px;width:220px;height:48px}

/* products */
.center-title{left:0;width:1200px;text-align:center}
.frame{position:absolute;border:1px solid var(--line)}
.frame-divider{position:absolute;top:0;bottom:0;left:487px;border-left:1.5px solid var(--line)}
.frame-knob{width:40px;height:40px;border:1px solid var(--line);background:var(--cream);left:468px;top:-21px}
.group-label{position:absolute;top:18px;font-size:14px;letter-spacing:2.5px;text-transform:uppercase}
.card{position:absolute;top:60px;height:282px}
.card-label{position:absolute;left:8px;right:8px;top:8px;height:42px;background:var(--label);display:flex;align-items:center;justify-content:center;font-size:12.5px;text-transform:uppercase;color:var(--ink)}
.view-all{left:490px;width:220px;height:48px}

/* newsletter */
.newsletter{position:absolute;left:112px;top:1886px;width:976px;height:406px;background:radial-gradient(ellipse at 50% 40%,#8c8782 0%,#7a746e 60%,#5f5954 100%)}
.newsletter-title{position:absolute;left:0;width:976px;top:48px;text-align:center;font-size:22px;line-height:40px;letter-spacing:1.5px;color:var(--white);text-transform:uppercase}
.field{position:absolute;top:159px;width:220px;height:42px;background:var(--white);font-size:11px;color:#aaa;padding-left:19px;display:flex;align-items:center;letter-spacing:.5px}
.interests{position:absolute;left:0;width:976px;top:232px;text-align:center;font-size:13px;letter-spacing:1px;color:var(--white);text-transform:uppercase}
.check{position:absolute;top:265px;display:flex;align-items:center;gap:19px;font-size:13px;letter-spacing:1px;color:var(--white);text-transform:uppercase}
.check i{display:block;width:22px;height:20px;background:var(--white)}
.newsletter .btn{left:378px;top:308px;width:220px;height:41px;font-size:13px}

/* shop */
.shop-photo{position:absolute;top:16px;width:461px;height:330px}
.shop-name{position:absolute;top:364px;width:487px;text-align:center;font-size:13px;text-transform:uppercase}
.shop-price{position:absolute;top:389px;width:487px;text-align:center;font-size:13px}

/* footer */
.site-footer{position:absolute;left:0;top:3044px;width:1200px;height:327px;background:var(--footer);color:var(--footer-text)}
.footer-col{position:absolute;top:62px}
.footer-col h4{font-size:15px;font-weight:400;text-transform:uppercase;margin-bottom:14px}
.footer-col li{list-style:none;font-size:12px;line-height:24px;text-transform:uppercase}
.copyright{position:absolute;left:0;top:3371px;width:1200px;height:60px;display:flex;align-items:center;justify-content:center;font-size:12.5px;letter-spacing:.5px;text-transform:uppercase}
</style>
</head>
<body>

<header class="site-header">
  <div class="utility">
    <span>Sign in or Register</span>
    <span><svg width="18" height="16" viewBox="0 0 18 16" fill="none" stroke="#8c8a87" stroke-width="1.3"><path d="M1 2h3l2 8h9l2-6H5"/><circle cx="7" cy="13.5" r="1.3"/><circle cx="14" cy="13.5" r="1.3"/></svg>(0) Items</span>
    <span><svg width="14" height="14" viewBox="0 0 14 14" fill="none" stroke="#8c8a87" stroke-width="1.6"><circle cx="5.5" cy="5.5" r="4"/><path d="M8.5 8.5l4 4"/></svg></span>
  </div>
  <div class="wordmark">Willow Lane</div>
  <nav class="main-nav">
    <a class="active" href="#">Home</a><a href="#">Sale</a><a href="#">New Arrivals</a><a href="#">Antique &amp; Unique</a><a href="#">Accessory</a><a href="#">Boutique</a><a href="#">Gift</a><a href="#">Gift Registry</a>
  </nav>
</header>

<section class="hero">
  <div class="hero-photo" role="img" aria-label="Ornate gilded armchair with green tufted upholstery against a grey wall"></div>
  <h1 class="hero-title">WILLOW LANE</h1>
  <p class="hero-text">Sed ut perspiciatis unde omnis iste natus error sit voluptatem accusantium</p>
  <a class="btn" href="#">Shop Now</a>
  <div class="circle hero-arrow" style="left:29px"><svg width="22" height="16" viewBox="0 0 22 16" fill="none" stroke="#fff" stroke-width="2"><path d="M21 8H2M8 1L1 8l7 7"/></svg></div>
  <div class="circle hero-arrow" style="left:1108px"><svg width="22" height="16" viewBox="0 0 22 16" fill="none" stroke="#fff" stroke-width="2"><path d="M1 8h19M14 1l7 7-7 7"/></svg></div>
</section>
<div class="circle scroll-down"><svg width="16" height="22" viewBox="0 0 16 22" fill="none" stroke="#555" stroke-width="1.6"><path d="M8 1v19M1 14l7 7 7-7"/></svg></div>

<section class="about">
  <div class="about-photo" role="img" aria-label="Antique brass mantel clock on a dark wooden table"></div>
  <h2 class="section-title about-title">About Us</h2>
  <p class="about-text">Sed ut perspiciatis unde omnis iste natus error sit voluptatem accusantium doloremque laudantium, totam rem aperiam, eaque ipsa quae ab illo inventore veritatis et quasi architecto beatae vitae dicta sunt explicabo. Nemo enim ipsam voluptatem quia voluptas sit aspernatur aut odit aut fugit, sed quia consequuntur magni dolores eos qui ratione voluptatem sequi nesciunt. Neque porro quisquam est, qui dolorem ipsum quia dolor sit amet, consectetur, adipisci velit, sed quia non numquam eius modi tempora incidunt ut labore et dolore magnam aliquam quaerat voluptatem.</p>
  <a class="btn" href="#">Read More</a>
</section>

<section class="products">
  <h2 class="section-title center-title" style="top:1278px">Our Products</h2>
  <div class="frame" style="left:112px;top:1351px;width:976px;height:361px">
    <div class="frame-divider"></div>
    <div class="circle frame-knob"><svg width="12" height="18" viewBox="0 0 12 18" fill="none" stroke="#555" stroke-width="1.4"><path d="M6 1v15M1 11l5 5 5-5"/></svg></div>
    <div class="group-label" style="left:0;width:487px;text-align:center">Antique</div>
    <div class="group-label" style="left:489px;width:487px;text-align:center">Unique</div>
    <div class="card" style="left:5px;width:233px;background:linear-gradient(180deg,#d9d2c6 0%,#a88a4e 55%,#5a3a22 100%)" role="img" aria-label="Large gold crown resting on antique books"><div class="card-label">Large Crown</div></div>
    <div class="card" style="left:248px;width:231px;background:linear-gradient(180deg,#3a3a3a 0%,#a07a48 55%,#2e2e2e 100%)" role="img" aria-label="Jewelled French crown on a dark stand"><div class="card-label">Larger French Crown</div></div>
    <div class="card" style="left:494px;width:232px;background:linear-gradient(180deg,#bdbdbd 0%,#9a9a98 50%,#6e5232 80%,#4a3a2a 100%)" role="img" aria-label="Vintage radio against a grey wall"><div class="card-label">Cloisonne Enamel Vase</div></div>
    <div class="card" style="left:735px;width:234px;background:linear-gradient(180deg,#f1ece6 0%,#e6ddd2 55%,#cdb892 80%,#efe9e2 100%)" role="img" aria-label="Golden upholstered chaise sofa in a pale room"><div class="card-label">Luxurious Golden Sofa</div></div>
  </div>
  <a class="btn view-all" style="top:1744px" href="#">View All</a>
</section>

<section class="newsletter">
  <h2 class="newsletter-title">Sign up to our newsletter<br>to stay up to date</h2>
  <div class="field" style="left:254px">YOUR NAME</div>
  <div class="field" style="left:502px">EMAIL ID</div>
  <div class="interests">Select additional interests</div>
  <label class="check" style="left:349px"><i></i>Antique</label>
  <label class="check" style="left:531px"><i></i>Unique</label>
  <a class="btn" href="#">Subscribe</a>
</section>

<section class="shop">
  <h2 class="section-title center-title" style="top:2370px">From the Shop</h2>
  <div class="frame" style="left:112px;top:2455px;width:976px;height:428px">
    <div class="frame-divider"></div>
    <div class="circle frame-knob"><svg width="12" height="18" viewBox="0 0 12 18" fill="none" stroke="#555" stroke-width="1.4"><path d="M6 1v15M1 11l5 5 5-5"/></svg></div>
    <div class="shop-photo" style="left:11px;background:linear-gradient(160deg,#e6e0d6 0%,#d2c9bb 55%,#8a6444 85%,#5a3a24 100%)" role="img" aria-label="Antique gramophone with a turquoise horn"></div>
    <div class="shop-photo" style="left:503px;background:radial-gradient(ellipse at 50% 55%,#d8cbb0 0%,#8a6a3a 50%,#3a2a18 100%)" role="img" aria-label="Gilded porcelain tea set with floral decoration"></div>
    <div class="shop-name" style="left:0">Turquoise Gramophone</div>
    <div class="shop-price" style="left:0">$450.00</div>
    <div class="shop-name" style="left:489px">Enim Adminima Veniam</div>
    <div class="shop-price" style="left:489px">$450.00</div>
  </div>
  <a class="btn view-all" style="top:2922px" href="#">View All</a>
</section>

<footer class="site-footer">
  <div class="footer-col" style="left:154px"><h4>Quick Links</h4><ul><li>Home</li><li>Sale</li><li>New Arrivals</li><li>Antique &amp; Unique</li><li>Accessory</li><li>Boutique</li><li>Gift</li><li>Gift Registry</li></ul></div>
  <div class="footer-col" style="left:393px"><h4>Special Events</h4><ul><li>Workshops</li><li>Private Events</li><li>Private Events Covent</li><li>Supper Clubs</li></ul></div>
  <div class="footer-col" style="left:667px"><h4>Terms and Conditions</h4><ul><li>Terms and Conditions</li><li>Privacy Policy</li><li>GDPR</li></ul></div>
  <div class="footer-col" style="left:972px"><h4>Social</h4><ul><li>Snapfolio</li><li>Friendhall</li><li>Pinboardly</li><li>Chirpline</li></ul></div>
</footer>
<div class="copyright">Copyright © 2021.&nbsp; All rights reserved</div>

</body>
</html>
```